Wesbite design for Investment Firm

We want a basic (clean) website that follows the form, fonts and colors of our attachments. This is for a financial investment management firm, but we have a boutique (anti-Wall Street) approach. Site should have an Home Page (Logo up top - room for basic copy on bottom, Philosophy Page (room for Quarterly Letter attachment and basic copy, Performance Page (room for Performance Overview and Performance Analysis and basic copy), Team Page, Commentary Page and Contact

Reason: Some designers have asked for an extension. Again, please only use image of Train Station or Train Station Logo in design.

Target Market(s)

Small and mid-size financial advisors from across the country

Industry/Entity Type

Financial

Number of Pages Required

5+ page

Font styles to use
Other font styles liked:
• Palotino Linotype

Colors
3176b5
cfdeed
ffffff

Requirements
Must have
• Please refer to existing site www.qlvor.example. Of note, this is too complex / cluttered. We simply want Blur, Grey and White consistent with attachments. The copy is pretty good, but will be simplified (and no quotes)
Should not have
• No images other than train station logo and / or train station image

```html
<!DOCTYPE html>
<html lang="en">
<head>
<meta charset="utf-8">
<title>Ashford Lane Investment Company</title>
<link href="https://fonts.googleapis.com/css2?family=Lora:wght@400&family=Open+Sans:wght@400&display=swap" rel="stylesheet">
<style>
:root{
  --ink:#2a3a5c;
  --blue:#3176b5;
  --pale:#cfdeed;
  --panel:#e9f0f7;
  --header-bg:#f4f7fa;
  --text:#555b61;
  --dark:#3b3b3b;
  --footer-text:#cfcfcf;
  --footer-mark:#8c8c8c;
  --rule:#d0d0d0;
  --white:#ffffff;
}
*{box-sizing:border-box;margin:0;padding:0}
html,body{width:782px;height:1200px;overflow:hidden;background:var(--white)}
body{position:relative;font-family:"Open Sans",Arial,sans-serif;color:var(--text)}
h1,h2{font-weight:400}
.abs{position:absolute}

/* header */
.site-header{left:0;top:0;width:782px;height:62px;background:var(--header-bg)}
.brand{left:86px;top:22px;display:flex;align-items:center;gap:7px}
.brand-square{width:9px;height:9px;background:var(--ink)}
.brand-name{font-family:"Lora",serif;font-size:16px;font-weight:400;color:var(--ink);line-height:1;white-space:nowrap}
.main-nav{right:87px;top:26px;display:flex;gap:19px;font-size:7.5px;color:var(--dark)}
.main-nav .current{color:var(--ink)}

/* hero */
.hero{left:0;top:62px;width:782px;height:271px;background:linear-gradient(180deg,#2f6bc4 0%,#7c8fa8 35%,#d9dde0 55%,#5d6a55 100%)}
.hero-label{left:86px;top:115px;width:102px;text-align:center;color:var(--white);font-family:"Lora",serif}
.hero-label .small{font-size:10px;line-height:1}
.hero-label .big{font-size:14px;line-height:1.2}
.letter-card{left:86px;top:148px;width:102px;height:131px;background:var(--white);border:1px solid #333}
.hero-arrow{top:190px;width:10px;height:14px}

/* welcome */
.welcome-title{left:0;top:368px;width:782px;text-align:center;font-family:"Lora",serif;font-size:23px;color:var(--blue)}
.welcome-text{left:86px;top:399px;width:610px;text-align:center;font-size:8.6px;line-height:14.5px}

/* quote */
.quote-band{left:86px;top:481px;width:609px;height:131px;background:linear-gradient(90deg,#3a77be,#4d86c7 60%,#3a77be)}
.quote-text{left:86px;top:516px;width:609px;text-align:center;color:var(--white);font-family:"Lora",serif;font-size:12.3px;line-height:18px}
.quote-source{left:86px;top:559px;width:609px;text-align:center;color:var(--white);font-family:"Lora",serif;font-size:10px}

/* commentary */
.section-title{left:85px;top:646px;font-family:"Lora",serif;font-size:22px;color:var(--blue)}
.pager{top:655px;width:15px;height:14px;border:1px solid #777;background:var(--white)}
.post{top:689px;width:178px}
.post-title{font-family:"Lora",serif;font-size:11px;color:#222}
.post-date{font-size:6.8px;color:#333;margin-top:3px;text-transform:uppercase}
.post-rule{height:2px;background:var(--rule);margin-top:12px}
.post-excerpt{font-size:5.7px;line-height:9.3px;color:#888;margin-top:10px}
.btn{display:inline-block;font-size:6px;color:#888;background:#f0f0f0;padding:6px 10px}
.post .btn{margin-top:10px}

/* features */
.features{left:86px;top:834px;width:609px;height:185px;background:var(--panel)}
.feature{top:870px;width:170px;text-align:center}
.feature svg{display:block;margin:0 auto}
.feature-title{font-family:"Lora",serif;font-size:10.5px;color:#222;margin-top:8px}
.feature-text{font-size:5.8px;line-height:9.3px;color:#444;margin-top:4px}
.feature .btn{background:var(--white);margin-top:9px}

/* footer */
.site-footer{left:0;top:1059px;width:782px;height:141px;background:var(--dark)}
.contact-line{left:86px;font-size:8px;color:var(--footer-text);display:flex;align-items:center;gap:7px}
.phone{font-size:13px}
.social{top:1141px;width:24px;height:24px;border:1px solid #9a9a9a;border-radius:50%}
.footer-nav{right:87px;top:1090px;font-size:6.6px;color:var(--footer-text);word-spacing:1px}
.copyright{right:87px;top:1108px;font-size:6.4px;color:var(--footer-text)}
.footer-brand{right:87px;top:1140px;display:flex;align-items:center;gap:7px}
.footer-brand .brand-square{background:var(--footer-mark)}
.footer-brand .name{font-family:"Lora",serif;font-size:16px;color:var(--footer-mark);line-height:1;white-space:nowrap}
</style>
</head>
<body>

<header class="abs site-header">
  <div class="abs brand">
    <span class="brand-square"></span>
    <span class="brand-name">Ashford Lane Investment Company</span>
  </div>
  <nav class="abs main-nav">
    <span class="current">Home</span><span>Philosophy</span><span>Performance</span><span>Team</span><span>Commentary</span><span>Contact</span>
  </nav>
</header>

<section class="abs hero" role="img" aria-label="Photograph of a white wooden train station with a shingled roof under a blue sky"></section>
<div class="abs hero-label"><div class="small">Investment Adviser's</div><div class="big">Letter</div></div>
<div class="abs letter-card" role="img" aria-label="Cover page of the investment adviser's letter"></div>
<svg class="abs hero-arrow" style="left:24px" viewBox="0 0 10 14"><path d="M8 1 2 7l6 6" fill="none" stroke="#fff" stroke-width="2.5"/></svg>
<svg class="abs hero-arrow" style="left:747px" viewBox="0 0 10 14"><path d="M2 1l6 6-6 6" fill="none" stroke="#fff" stroke-width="2.5"/></svg>

<h1 class="abs welcome-title">Welcome</h1>
<p class="abs welcome-text">We founded Ashford Lane Investment Company in 1999, initially managing wealth from our family and friends in the town of Ashford. The high expectations of our original investors is a key contributor to our value driven investment philosophy. Based in Dallas, TX, we manage assets for both individuals and institutions. Our investment methodology stresses absolute returns vs. relative performance, blending a combination of fundamental analysis, discipline and patience with the goal of preserving and compounding capital.</p>

<div class="abs quote-band" role="img" aria-label="Faint blue-toned image of stacked coins before a city skyline"></div>
<p class="abs quote-text">"A sound investment is one which, after careful study, offers real protection of capital<br>and a fair reward. Anything that fails these tests is a wager, not an investment."</p>
<p class="abs quote-source">- Harold Wexley, The Patient Investor</p>

<h2 class="abs section-title">Latest Commentary</h2>
<svg class="abs pager" style="left:660px" viewBox="0 0 15 14"><path d="M9 4 6 7l3 3" fill="none" stroke="#555" stroke-width="1"/></svg>
<svg class="abs pager" style="left:680px" viewBox="0 0 15 14"><path d="M6 4l3 3-3 3" fill="none" stroke="#555" stroke-width="1"/></svg>

<article class="abs post" style="left:86px">
  <div class="post-title">Core Equity Portfolio – Q2 2017</div>
  <div class="post-date">August 10, 2017</div>
  <div class="post-rule"></div>
  <p class="post-excerpt">Based on our estimate of fair value relative to the company's current stock price, we determine each company's current margin of safety in the Core Equity ...</p>
  <span class="btn">Read more</span>
</article>
<article class="abs post" style="left:302px">
  <div class="post-title">Core Equity Portfolio – Q2 2017</div>
  <div class="post-date">August 10, 2017</div>
  <div class="post-rule"></div>
  <p class="post-excerpt">Based on our estimate of fair value relative to the company's current stock price, we determine each company's current margin of safety in the Core Equity ...</p>
  <span class="btn">Read more</span>
</article>
<article class="abs post" style="left:517px">
  <div class="post-title">Core Equity Portfolio – Q2 2017</div>
  <div class="post-date">August 10, 2017</div>
  <div class="post-rule"></div>
  <p class="post-excerpt">Based on our estimate of fair value relative to the company's current stock price, we determine each company's current margin of safety in the Core Equity ...</p>
  <span class="btn">Read more</span>
</article>

<section class="abs features"></section>
<div class="abs feature" style="left:95px">
  <svg width="26" height="22" viewBox="0 0 26 22"><ellipse cx="13" cy="9" rx="12" ry="8.5" fill="#555"/><path d="M5 14 3 21l8-5z" fill="#555"/></svg>
  <div class="feature-title">Philosophy</div>
  <p class="feature-text">Phasellus nisl est, condimentum vitae faucibus in, sollicitudin vel metus. Nunc sit amet consequat risus. Curabitur ac elit leo. In eleifend dui tellus</p>
  <span class="btn">Read more</span>
</div>
<div class="abs feature" style="left:305px">
  <svg width="26" height="22" viewBox="0 0 26 22"><circle cx="10" cy="12" r="7" fill="none" stroke="#555" stroke-width="4" stroke-dasharray="3 2"/><circle cx="10" cy="12" r="2" fill="#555"/><circle cx="20" cy="5" r="3.5" fill="none" stroke="#555" stroke-width="2.5" stroke-dasharray="2 1.5"/><circle cx="20" cy="17" r="3.5" fill="none" stroke="#555" stroke-width="2.5" stroke-dasharray="2 1.5"/></svg>
  <div class="feature-title">Performance</div>
  <p class="feature-text">Phasellus nisl est, condimentum vitae faucibus in, sollicitudin vel metus. Nunc sit amet consequat risus. Curabitur ac elit leo. In eleifend dui tellus</p>
  <span class="btn">Read more</span>
</div>
<div class="abs feature" style="left:515px">
  <svg width="26" height="22" viewBox="0 0 26 22" fill="#555"><circle cx="7" cy="5" r="3.5"/><circle cx="19" cy="5" r="3.5"/><circle cx="13" cy="9" r="4"/><rect x="1" y="10" width="8" height="6" rx="2"/><rect x="17" y="10" width="8" height="6" rx="2"/><rect x="6" y="14" width="14" height="8" rx="3"/></svg>
  <div class="feature-title">Team</div>
  <p class="feature-text">Phasellus nisl est, condimentum vitae faucibus in, sollicitudin vel metus. Nunc sit amet consequat risus. Curabitur ac elit leo. In eleifend dui tellus</p>
  <span class="btn">Read more</span>
</div>

<footer class="abs site-footer"></footer>
<div class="abs contact-line" style="top:1088px">
  <svg width="6" height="8" viewBox="0 0 6 8"><path d="M3 0a3 3 0 0 1 3 3c0 2-3 5-3 5S0 5 0 3a3 3 0 0 1 3-3z" fill="#cfcfcf"/></svg>
  <span>2710 Birchwood Avenue, Suite 820 Dallas, TX 75201</span>
</div>
<div class="abs contact-line" style="top:1101px">
  <svg width="6" height="5" viewBox="0 0 6 5"><rect width="6" height="5" fill="#cfcfcf"/><path d="M0 0l3 3 3-3" fill="none" stroke="#3b3b3b" stroke-width=".7"/></svg>
  <span>info@qlvor.example</span>
</div>
<div class="abs contact-line phone" style="top:1116px">
  <svg width="9" height="10" viewBox="0 0 9 10"><path d="M1 1l2-1 1.5 2.5L3 4q1 2 3 3l1.5-1.5L9 7 8 9Q4 10 1 5.5 0 3 1 1z" fill="#cfcfcf"/></svg>
  <span>214.555.0148</span>
</div>
<div class="abs social" style="left:86px"></div>
<div class="abs social" style="left:118px"></div>
<div class="abs social" style="left:149px"></div>
<div class="abs social" style="left:180px"></div>
<div class="abs footer-nav">Home &nbsp;|&nbsp; Philosophy &nbsp;|&nbsp; Performance &nbsp;|&nbsp; Team &nbsp;|&nbsp; Commentary &nbsp;|&nbsp; Contact</div>
<div class="abs copyright">Copyright © 2017 Ashford Lane Investment Company. &nbsp;All rights reserved.</div>
<div class="abs footer-brand">
  <span class="brand-square"></span>
  <span class="name">Ashford Lane Investment Company</span>
</div>

</body>
</html>
```